Flyer Design Project for Sports Medicine Services

I am a sports medicine doctor specialising in the diagnosis and management of sport and exercise injuries for all ages and levels of activity - from elite to weekend jogger. I work under the Business name Peak Stride Athletics and do have a company logo. I am wanting a flier that I can send to family doctors, physiotherapists and sports clubs explaining who I am what I can offer and why they should send me patients.
- I have a Masters in Sports Medicine (MSportsMed), Diplomas in Obstetrics/Gynaecology (DRANZCOG) and also Paediatrics (DCH) and certificate in advanced clinical hypnosis
-accurate diagnosis and management plan with their regular physio to return the player / athlete to the field / court /gym as soon as safely possible
-hypnosis for sports performance eg anxiety control, confidence and mental rehearsal for individuals and teams
- because there are many possible therapists and therapy options, as a sports doctor I can work out who they need to see a physiotherapist, surgeon, massage therapist chiropractor or podiatrist to return them to activity or whether cortisone, PRP or autologous blood injections are needed
-can provide one point of contact for coaches and clubs for rehabilitation and return to sport advice.
- work with Laura Pemberton ex Australian Athlete, a Performance Strategist (NLB listed resource person) and registered Psychologist for best mental preparation for individuals teams and coach development
- can organise rapid access to MRI, ultrasound and specialist appointments if needed
-I work at 3 practices KinetaCare 518 Hollis Rd Hollis 84619027 Monday Wednesday Friday; Brackley Sports Clinic, 193 Brackley Rd, Adelaide 81946372 Tuesday Riverton Hawks Sports Medicine Clinic, Tolvane Arena 8162 5907 Thursday.
-facebook site peakstrideathletics
Updates
Hi All, just to clarify.. My name is Simon Drewett and I am the sports doctor. My wife is Laura Pemberton and she is the psychologist. The flier should mainly be advertising my sports medicine services and a byline ( or at least not the first line in the title) about the Performance Strategy and Coach development.
Target Market(s)
family doctors (GPs), Sporting Clubs, Physiotherapists
Industry/Entity Type
Massage
Look and feel

```html
<!DOCTYPE html>
<html lang="en">
<head>
<meta charset="utf-8">
<title>Peak Stride Athletics – Sports Medicine Flyer</title>
<link rel="stylesheet" href="https://fonts.googleapis.com/css2?family=Arimo:wght@700&family=Noto+Sans:wght@400;800&family=Ubuntu:wght@300;400;500&display=swap">
<style>
  :root {
    --ink: #000000;
    --sky: #2ba6df;
    --lime: #b4d235;
    --lime-ink: #2f3b10;
    --white: #ffffff;
    --bone-blue: #2a6fd6;
    --deep-blue: #06122e;
  }
  * { box-sizing: border-box; margin: 0; padding: 0; }
  html, body { width: 847px; height: 1200px; overflow: hidden; background: #f2f2f2; }
  .flyer {
    position: relative;
    width: 847px; height: 1200px;
    background: var(--ink);
    overflow: hidden;
  }

  /* Header */
  .header { position: absolute; left: 0; top: 0; width: 847px; height: 428px; }
  .brand {
    position: absolute; left: 40px; top: 150px; width: 340px;
    text-align: center;
  }
  .brand-dot {
    display: block; width: 92px; height: 92px; margin: 0 auto 28px;
    border-radius: 50%; background: var(--lime);
  }
  .brand-name {
    font-family: "Ubuntu", sans-serif; font-weight: 500;
    font-size: 38px; line-height: 42px; color: var(--sky);
    letter-spacing: -0.5px;
  }
  .hero-visual {
    position: absolute; left: 408px; top: 0; width: 439px; height: 428px;
    background:
      radial-gradient(ellipse 60px 110px at 52% 72%, rgba(230,40,60,0.75), rgba(230,40,60,0) 100%),
      radial-gradient(ellipse at 55% 45%, var(--bone-blue) 0%, #153a8a 45%, var(--deep-blue) 80%, var(--ink) 100%);
  }

  /* Title band */
  .title-band {
    position: absolute; left: 0; top: 428px; width: 847px; height: 150px;
    background: var(--sky);
    display: flex; flex-direction: column; justify-content: center; align-items: center;
    font-family: "Arimo", sans-serif; font-weight: 700; color: var(--white);
    font-size: 43px; line-height: 55px; text-align: center;
  }

  /* Body */
  .services { position: absolute; left: 0; top: 578px; width: 847px; height: 502px; }
  .intro {
    position: absolute; left: 51px; right: 43px; top: 34px;
    font-family: "Noto Sans", sans-serif; font-weight: 800;
    font-size: 23.5px; line-height: 29px; color: var(--white);
    text-align: justify; hyphens: manual;
  }
  .offer-list {
    position: absolute; left: 51px; right: 40px; top: 200px;
    list-style: none;
    font-family: "Noto Sans", sans-serif; font-weight: 400;
    font-size: 16.6px; line-height: 25px; color: var(--white);
  }
  .offer-list li {
    position: relative; padding-left: 20px; margin-bottom: 25px;
    text-align: justify;
  }
  .offer-list li::before {
    content: ""; position: absolute; left: 0; top: 8px;
    width: 11px; height: 11px; border-radius: 50%; background: var(--lime);
  }

  /* Locations footer */
  .locations {
    position: absolute; left: 0; top: 1080px; width: 847px; height: 120px;
    background: var(--lime); color: var(--lime-ink);
    font-family: "Ubuntu", sans-serif;
  }
  .location { position: absolute; top: 12px; }
  .location + .location::before {
    content: ""; position: absolute; left: -17px; top: 0; width: 1px; height: 96px;
    background: var(--white);
  }
  .location.one { left: 40px; }
  .location.two { left: 278px; }
  .location.three { left: 513px; }
  .days { font-weight: 300; font-size: 14.5px; line-height: 20px; }
  .clinic { font-weight: 500; font-size: 17px; line-height: 22px; margin-top: 2px; }
  .address { font-weight: 400; font-size: 14.5px; line-height: 19px; }
  .phone { font-weight: 500; font-size: 15px; line-height: 20px; }
</style>
</head>
<body>
<main class="flyer">
  <header class="header">
    <div class="brand">
      <span class="brand-dot"></span>
      <div class="brand-name">Peak Stride Athletics</div>
    </div>
    <div class="hero-visual" role="img" aria-label="Glowing blue x-ray style illustration of a human torso and spine with a red highlight on the lower back"></div>
  </header>

  <section class="title-band">
    <h1 style="font:inherit">Sport Injuries Diagnosis &amp; Treatment</h1>
    <h2 style="font:inherit">High Performance Psychology</h2>
  </section>

  <section class="services">
    <p class="intro">Simon Drewett a Sports Medicine and Exercise Injuries Doctor specialising in the diagnosis and management of sport and exercise injuries for all ages and levels of ac-tivity - from elite to weekend jogger.</p>
    <ul class="offer-list">
      <li>Simon has a Masters in Sports Medicine (MSportsMed), Diplomas in Obstetrics /Gynaecology (DRANZCOG) and also Paediatrics (DCH) and certificate in advanced clini-cal hypnosis</li>
      <li>Accurate diagnosis and management plan with their regular physio to return the player / athlete to the field / court /gym as soon as safely possible</li>
      <li>Hypnosis for sports performance eg anxiety control, confidence and mental rehearsal for individuals and teams</li>
      <li>Rapid access to specialists if needed. Rapid referrals for MRI ultrasound and xrays</li>
    </ul>
  </section>

  <footer class="locations">
    <div class="location one">
      <div class="days">Monday, Wednesday,&nbsp; Friday</div>
      <div class="clinic">KinetaCare</div>
      <div class="address">518 Hollis Rd Hollis</div>
      <div class="phone">84619027</div>
    </div>
    <div class="location two">
      <div class="days">Tuesday</div>
      <div class="clinic">Brackley Sports Clinic</div>
      <div class="address">193 Brackley Rd, Adelaide</div>
      <div class="phone">81946372</div>
    </div>
    <div class="location three">
      <div class="days">Thursday</div>
      <div class="clinic">Riverton Hawks Sports Medicine Clinic</div>
      <div class="address">Tolvane Arena</div>
      <div class="phone">8162 5907</div>
    </div>
  </footer>
</main>
</body>
</html>
```